high end kitchens , needing new logo and business card design .

im looking a very simple looking design but classy that will stand out , i would like the design to be in the colours black , silver , gold and grey , although all colours dont need to be used in design , back of card to have name on it derek fawcett , address and phone number and website address , maybe fb logo . adrress is 42 mill row , kestrelford , bt19 4qa , 07912488265 , front of the card im open to design , back of card very simple i will want it matt black with silver writing , writing doesnt need to be that big

Target Market(s)

people with kitchen projects .

Industry/Entity Type

Interior Design

Contact Information for Business Card

front of business card th on it with maybe tallow hearths under it wrote smaller , maybe the card to be mate black with the writing in a gloss black or silver

Logo Text

th . tallow hearths

Font styles to use
Sans Serif
Script

Colors
1b1b1b
919191
f6f6f6
848484
ffc214
ec1f27

Requirements
Must have
• clean and simple , not too fussy ,
Nice to have
• n/a
Should not have
• n/a

```html
<!DOCTYPE html>
<html lang="en">
<head>
<meta charset="utf-8">
<title>Tallow Hearths – Business Card</title>
<link rel="stylesheet" href="https://fonts.googleapis.com/css2?family=Jost:wght@400;500&display=swap">
<style>
  :root {
    --backdrop: #141414;
    --card-black: #1b1b1b;
    --emboss-grey: #848484;
    --silver: #919191;
    --paper-white: #f6f6f6;
    --gold: #ffc214;
  }
  * { box-sizing: border-box; margin: 0; padding: 0; }
  html, body {
    width: 1200px;
    height: 900px;
    overflow: hidden;
    background: var(--backdrop);
    font-family: "Jost", "Futura", sans-serif;
  }
  .sheet {
    width: 1200px;
    height: 900px;
    display: flex;
    flex-direction: column;
    align-items: center;
    justify-content: center;
    gap: 40px;
  }
  .card {
    position: relative;
    width: 660px;
    height: 380px;
    background: var(--card-black);
    border-bottom: 6px solid var(--gold);
    box-shadow: 0 14px 30px rgba(0, 0, 0, 0.55);
  }
  .card--front {
    display: flex;
    align-items: center;
    justify-content: center;
  }
  .wordmark {
    color: var(--emboss-grey);
    font-weight: 400;
    text-transform: uppercase;
    letter-spacing: 0.04em;
    white-space: nowrap;
  }
  .card--front .wordmark { font-size: 52px; }

  .card--back {
    display: flex;
    align-items: center;
    padding: 0 40px;
  }
  .brand-block {
    width: 290px;
    display: flex;
    justify-content: center;
  }
  .card--back .wordmark { font-size: 30px; }
  .divider {
    width: 2px;
    height: 180px;
    background: var(--gold);
    margin: 0 34px 0 20px;
  }
  .contact { color: var(--paper-white); }
  .contact__name {
    color: var(--gold);
    font-size: 24px;
    font-weight: 400;
    text-transform: uppercase;
    letter-spacing: 0.06em;
    margin-bottom: 14px;
    white-space: nowrap;
  }
  .contact__line {
    font-size: 18px;
    line-height: 1.3;
    letter-spacing: 0.04em;
    white-space: nowrap;
  }
  .contact__address { margin-top: 10px; }
</style>
</head>
<body>
  <main class="sheet">
    <section class="card card--front" aria-label="Card front">
      <p class="wordmark">Tallow Hearths</p>
    </section>

    <section class="card card--back" aria-label="Card back">
      <div class="brand-block">
        <p class="wordmark">Tallow Hearths</p>
      </div>
      <div class="divider" aria-hidden="true"></div>
      <div class="contact">
        <h1 class="contact__name">Derek Fawcett</h1>
        <p class="contact__line">07912488265</p>
        <p class="contact__line">info@tallowhearths.com</p>
        <p class="contact__line">www.tallowhearths.com</p>
        <div class="contact__address">
          <p class="contact__line">42 mill row ,</p>
          <p class="contact__line">kestrelford , bt19 4qa</p>
        </div>
      </div>
    </section>
  </main>
</body>
</html>
```